Silent Disco and Photo Booth Magazine Advertisements

We have two one-page advertisement placements in a magazine that is being distributed to thousands of people at a large Christian camp. We are targeting all the folks reading the ad, but especially want this catered to Youth Pastors, who are the ones who would make the buying decision on renting equipment from us. They need to have the exact same feel and vibe, hence being made together here.

We want one of these full-page advertisements to feature our Silent Disco Headsets, and the other to be focused on our Photo Booths. Our company rents and ships event equipment nationally as our primary service, and we want to feature that as the focus.

We are a fun company, provide fun entertainment equipment services, and take a 100% satisfaction approach to our customer service. We have a long-standing reputation for providing equipment that will be a guaranteed successful event and always arrive on time. It's easy, fun, and a fair value.

Attached are two mock-ups of some ideas we have around it. Some content options are below:

***Silent Disco Rentals***
Rentals starting at $5 per person (plus the cost of shipping)
Easy to setup
Works well for prayer and for silent disco fun
Guarantee to get everyone out for a fun time
Nation's biggest silent disco provider
50 or 5,000 we got you covered
Go to gleamtunes.net/outings/chapel/ to find our youth pastor event guide

**Photo booth**
Shippability (national)
Portability (very portable)
Setup in 5 minutes
Social fun aspect
Social sharing aspect (Snapwell/Friendora)
Full branding: Use for contests, promotions, special sponsorships
KRAV special starting at $679 (crossed out $479) for 2022
Save $200 off of every order

PLEASE USE THESE COLORS:
Colors:
Pink- HEX #CC008F
HEX # 690065
Black- HEX #000000

Font:
Font- Montserrat (Primary)
Roboto (Secondary)

Target Market(s)

Youth Pastors, Pastors, Church Event Managers, Church Activity Directors 18-40 years old

Font styles to use
Other font styles liked:
• Font- Montserrat (Primary) Roboto (Secondary) (Pink- HEX #CC008F HEX # 690065 Black- HEX #000000)

Colors

Designer to choose colors to be used in the design.

Requirements
Must have
• Crisp, clear, call to action, explanation of offerings, great theme. Font- Montserrat (Primary) Roboto (Secondary) Pink- HEX #CC008F HEX # 690065 Black- HEX #000000

```html
<!DOCTYPE html>
<html lang="en">
<head>
<meta charset="UTF-8">
<title>Silent Disco Rentals</title>
<link href="https://fonts.googleapis.com/css2?family=Montserrat:wght@500;700;800;900&family=Roboto:wght@400;500;700&display=swap" rel="stylesheet">
<style>
  :root {
    --pink: #cc008f;
    --plum: #690065;
    --black: #000000;
    --white: #ffffff;
    --ink: #1a1a1a;
    --night: #1b0420;
  }
  * { margin: 0; padding: 0; box-sizing: border-box; }
  html, body { width: 744px; height: 1200px; overflow: hidden; background: #e9e9e9; }
  .ad {
    position: relative; width: 744px; height: 1200px; overflow: hidden;
    font-family: "Montserrat", sans-serif; background: var(--black);
  }
  .hero {
    position: absolute; left: 0; top: 0; width: 744px; height: 540px;
    background:
      radial-gradient(ellipse 320px 200px at 372px 470px, rgba(255,80,190,.55), transparent 70%),
      radial-gradient(ellipse 260px 260px at 120px 120px, rgba(204,0,143,.55), transparent 70%),
      radial-gradient(ellipse 260px 260px at 640px 140px, rgba(140,40,220,.55), transparent 70%),
      linear-gradient(180deg, var(--night) 0%, var(--plum) 55%, #a3007a 100%);
  }
  .brand {
    position: absolute; top: 46px; left: 0; width: 100%;
    display: flex; justify-content: center; align-items: center; gap: 16px;
  }
  .brand-dot { width: 46px; height: 46px; border-radius: 50%; background: var(--white); }
  .brand-name { font-weight: 900; font-size: 46px; color: var(--white); letter-spacing: 1px; }
  .headline {
    position: absolute; top: 150px; width: 100%; text-align: center;
    font-weight: 900; font-size: 92px; line-height: 1; color: var(--white);
    letter-spacing: 1px; text-transform: uppercase; white-space: nowrap;
  }
  .sub-pill {
    position: absolute; top: 262px; left: 50%; transform: translateX(-50%);
    background: var(--white); color: var(--pink); border-radius: 16px;
    font-weight: 900; font-size: 54px; padding: 4px 34px; letter-spacing: 2px;
  }
  .price-box {
    position: absolute; top: 390px; width: 200px; height: 118px;
    background: var(--white); display: flex; flex-direction: column;
    justify-content: center; align-items: center; text-align: center;
  }
  .price-box.cost { left: 36px; }
  .price-box.rate { right: 36px; }
  .price-big { font-weight: 900; font-size: 46px; line-height: 1; color: var(--pink); }
  .price-small { font-weight: 800; font-size: 20px; color: var(--black); margin-top: 4px; }
  .band {
    position: absolute; left: 0; width: 100%; background: var(--pink);
    color: var(--white); text-align: center; font-weight: 900; text-transform: uppercase;
    white-space: nowrap;
  }
  .band.starting { top: 540px; height: 62px; line-height: 62px; font-size: 38px; letter-spacing: 1px; }
  .details { position: absolute; top: 602px; left: 0; width: 744px; height: 300px; background: var(--white); }
  .setup-tag {
    position: absolute; top: 26px; left: 36px; border: 4px solid var(--black);
    padding: 6px 18px; font-weight: 900; font-size: 40px; line-height: 1.02;
    color: var(--black); text-transform: uppercase; white-space: nowrap;
  }
  .setup-tag span { color: var(--pink); display: block; }
  .setup-copy {
    position: absolute; top: 34px; left: 290px; width: 410px;
    font-family: "Roboto", sans-serif; font-weight: 500; font-size: 21px;
    line-height: 1.35; color: var(--ink);
  }
  .gear {
    position: absolute; left: 120px; top: 140px; width: 590px; height: 150px;
    border-radius: 8px;
    background: linear-gradient(90deg, #2a2a2a 0%, #555 45%, #bdbdbd 70%, #e0e0e0 100%);
  }
  .footer { position: absolute; top: 902px; left: 0; width: 744px; height: 298px; background: var(--black); }
  .claim {
    position: absolute; top: 38px; left: 0; width: 100%; text-align: center;
    font-weight: 900; font-size: 28px; line-height: 1.2; color: var(--white);
    text-transform: uppercase; white-space: nowrap;
  }
  .claim em { font-style: normal; color: var(--pink); }
  .band.covered { top: 104px; height: 80px; line-height: 80px; font-size: 33px; }
  .guide {
    position: absolute; top: 226px; left: 0; width: 100%; text-align: center;
    font-family: "Roboto", sans-serif; font-size: 18px; line-height: 1.3;
    color: var(--white); white-space: nowrap;
  }
</style>
</head>
<body>
<main class="ad">
  <section class="hero" role="img" aria-label="Dark stage lit with pink and purple disco lights">
  </section>
  <div class="brand">
    <span class="brand-dot"></span>
    <span class="brand-name">GLEAMTUNES</span>
  </div>
  <h1 class="headline">Silent Disco</h1>
  <div class="sub-pill">RENTALS</div>

  <div class="price-box cost">
    <div class="price-big">COST</div>
    <div class="price-small">OF SHIPPING</div>
  </div>
  <div class="price-box rate">
    <div class="price-big">$5</div>
    <div class="price-small">PER PERSON</div>
  </div>

  <div class="band starting">Rentals starting at</div>

  <section class="details">
    <div class="setup-tag">Easy to<span>Setup</span></div>
    <p class="setup-copy">Works well for prayer and for silent disco fun. Guarantee to get everyone out for a fun time.</p>
    <div class="gear" role="img" aria-label="Silent disco headsets and transmitter"></div>
  </section>

  <section class="footer">
    <p class="claim">Nation's biggest <em>silent disco</em> provider</p>
    <div class="band covered">50 or 5,000 we got you covered</div>
    <p class="guide">Go to gleamtunes.net/outings/chapel/ to find our youth pastor event guide</p>
  </section>
</main>
</body>
</html>
```